Wallet/Purse themed website design

We need a simple but visually stunning graphic design for a new web based company called "thecardvaultly.com".

TheCardVaultly is an online/phone app offering extremely secure backup/storage for our users' personal documentation, such as credit cards, ID, passports, certificates, insurance etc.

Documents will be uploaded via a mobile app (initially zPad) to the storage. Retrieval is only possible via login together with bank level authentication (using personal questions).

Our service will not prevent the theft of our customer's physical wallet however our retrieval service can be accessed anywhere online and assist with the replacement. (for example a lost passport will require a new passport request which requires details of the lost passport number/details).
The key audiences for TheCardVaultly include holidaymakers, businessmen, individuals, banking customers

We have specified that the initial design needs only to have 3 pages - home page, login page, wallet contents retrieval page.

Common themes of the following should be strongly brought to bear on the pages:
-Leather wallet/stitching
-Secure/safe/private/encryted
-Personal - for example family holiday
-Access anywhere
-Pick pockets can easily steal your wallet
Updates

Thank you for all of your submissions!  This was our first attempt to source a design via Pixel Bazaar and we will certainly use this resource again.

Thank you.

Target Market(s)

Industry/Entity Type

Graphic Design

Requirements
Must have
• 3 pages - home page, login page, wallet contents retrieval page.
Nice to have
• Modern UI design appealing to families and individuals

```html
<!DOCTYPE html>
<html lang="en">
<head>
<meta charset="utf-8">
<title>thecardvaultly.com – Web Pages</title>
<link rel="stylesheet" href="https://fonts.googleapis.com/css2?family=Hind:wght@500;600&display=swap">
<style>
  :root {
    --sky-blue: #0049a0;
    --sky-blue-light: #0a58b4;
    --floor-dark: #050d1c;
    --panel-orange: #f26522;
    --button-blue: #0b4b9b;
    --field-white: #ffffff;
    --text-white: #ffffff;
    --brand-gold: #f5a623;
    --photo-light: #f4f1ee;
    --photo-mid: #c9a58e;
  }
  * { box-sizing: border-box; margin: 0; padding: 0; }
  html, body { width: 1200px; height: 900px; overflow: hidden; }
  body {
    position: relative;
    font-family: "Hind", Arial, sans-serif;
    color: var(--text-white);
    background: radial-gradient(ellipse at 50% 40%, var(--sky-blue-light), var(--sky-blue) 70%);
  }
  .floor { position: absolute; left: 0; top: 0; width: 1200px; height: 900px; }
  .site-name {
    position: absolute; top: 66px; left: 0; width: 1200px;
    text-align: center; font-size: 68px; font-weight: 600;
    color: var(--brand-gold); letter-spacing: 1px; line-height: 1;
  }
  .panel {
    position: absolute; top: 158px; height: 557px;
    background: var(--panel-orange);
    box-shadow: 4px 6px 10px rgba(0,0,0,0.55);
  }
  .panel-brand { left: 77px; width: 341px; }
  .panel-login { left: 436px; width: 327px; }
  .panel-home { left: 780px; width: 339px; }
  .panel-title {
    position: absolute; top: 13px; font-size: 33px; font-weight: 500; line-height: 1.2;
  }
  .panel-icon { position: absolute; }
  .photo-area {
    position: absolute; left: 25px; top: 88px; width: 289px; height: 266px;
    background: linear-gradient(135deg, var(--photo-light) 35%, var(--photo-mid) 60%, var(--photo-light) 85%);
  }
  .service-icons { position: absolute; left: 0; top: 383px; width: 341px; height: 50px; }
  .footer-links {
    position: absolute; top: 512px; font-size: 19px; font-weight: 500;
  }
  .field-label { position: absolute; left: 7px; font-size: 26px; font-weight: 500; line-height: 1; }
  .field-input {
    position: absolute; left: 143px; width: 172px; height: 29px;
    background: var(--field-white); border: none;
  }
  .action-button {
    position: absolute; height: 31px; background: var(--button-blue);
    color: var(--text-white); font-family: inherit; font-size: 25px; font-weight: 500;
    border: none; line-height: 34px; text-align: center;
  }
  .detail-label { position: absolute; left: 34px; font-size: 26px; font-weight: 500; line-height: 1; }
</style>
</head>
<body>
  <svg class="floor" viewBox="0 0 1200 900" aria-hidden="true">
    <defs>
      <filter id="floor-soften"><feGaussianBlur stdDeviation="6"/></filter>
    </defs>
    <g filter="url(#floor-soften)" fill="var(--floor-dark)">
      <polygon points="60,810 150,770 440,770 410,900 40,900"/>
      <polygon points="455,770 780,768 760,900 430,900"/>
      <polygon points="798,766 1120,730 1200,725 1200,900 780,900"/>
    </g>
    <g filter="url(#floor-soften)" fill="var(--floor-dark)" opacity="0.85">
      <polygon points="0,900 0,860 60,810 40,900"/>
    </g>
  </svg>

  <div class="site-name">thecardvaultly.com</div>

  <section class="panel panel-brand">
    <h2 class="panel-title" style="left:16px;">Card Vaultly</h2>
    <svg class="panel-icon" style="left:254px;top:8px;" width="72" height="50" viewBox="0 0 72 50" aria-hidden="true">
      <g fill="none" stroke="var(--button-blue)" stroke-width="4">
        <path d="M2 4 H12 L18 32 H62 L68 10 H14"/>
        <path d="M24 10 V32 M34 10 V32 M44 10 V32 M54 10 V32 M16 21 H66"/>
      </g>
      <circle cx="24" cy="42" r="5" fill="var(--button-blue)"/>
      <circle cx="56" cy="42" r="5" fill="var(--button-blue)"/>
    </svg>
    <div class="photo-area" role="img" aria-label="Photo of a couple smiling at a laptop"></div>
    <svg class="service-icons" viewBox="0 0 341 50" aria-hidden="true">
      <g fill="none" stroke="var(--text-white)" stroke-width="2.5">
        <rect x="26" y="8" width="66" height="36"/>
        <path d="M26 8 L59 30 L92 8 M26 44 L50 25 M92 44 L68 25"/>
        <circle cx="151" cy="26" r="26"/>
        <ellipse cx="151" cy="26" rx="12" ry="26"/>
        <path d="M125 26 H177 M129 13 H173 M129 39 H173 M151 0 V52"/>
        <circle cx="222" cy="23" r="20"/>
        <ellipse cx="222" cy="23" rx="9" ry="20"/>
        <path d="M202 23 H242 M205 13 H239 M205 33 H239"/>
        <circle cx="237" cy="31" r="10" fill="var(--panel-orange)" stroke-width="3"/>
        <path d="M244 38 L262 50" stroke-width="6"/>
        <circle cx="295" cy="26" r="17"/>
        <path d="M295 16 V36 M285 26 H305" stroke-width="4"/>
      </g>
    </svg>
    <span class="footer-links" style="left:11px;">Contact</span>
    <span class="footer-links" style="left:139px;">About Us</span>
    <span class="footer-links" style="left:278px;">Store</span>
  </section>

  <section class="panel panel-login">
    <h2 class="panel-title" style="left:18px;">Secure Login</h2>
    <svg class="panel-icon" style="left:222px;top:8px;" width="92" height="50" viewBox="0 0 92 50" aria-hidden="true">
      <g fill="var(--button-blue)">
        <circle cx="70" cy="24" r="20"/>
        <path d="M4 20 H54 V30 H44 V36 H36 V30 H28 V38 H18 V30 H4 Z"/>
      </g>
      <circle cx="74" cy="18" r="5" fill="var(--panel-orange)"/>
    </svg>
    <span class="field-label" style="top:90px;">Username</span>
    <span class="field-input" style="top:86px;"></span>
    <span class="field-label" style="top:145px;">Password</span>
    <span class="field-input" style="top:138px;"></span>
    <span class="field-label" style="top:201px;">Question</span>
    <span class="field-input" style="top:194px;"></span>
    <span class="field-label" style="top:259px;">Answers</span>
    <span class="field-input" style="top:252px;"></span>
    <span class="action-button" style="left:85px;top:322px;width:132px;">Submit</span>
  </section>

  <section class="panel panel-home">
    <h2 class="panel-title" style="left:31px;">Home Page</h2>
    <svg class="panel-icon" style="left:233px;top:8px;" width="64" height="46" viewBox="0 0 64 46" aria-hidden="true">
      <g fill="none" stroke="var(--text-white)" stroke-width="3">
        <path d="M3 20 L32 3 L61 20 Z"/>
        <rect x="9" y="20" width="46" height="24"/>
        <rect x="16" y="27" width="10" height="17"/>
        <rect x="34" y="27" width="14" height="9"/>
      </g>
    </svg>
    <span class="detail-label" style="top:90px;">Name</span>
    <span class="detail-label" style="top:144px;">Details</span>
    <span class="action-button" style="left:24px;top:194px;width:131px;">Back</span>
    <span class="action-button" style="left:179px;top:191px;width:131px;">Next</span>
    <span class="action-button" style="left:24px;top:278px;width:131px;">Edit</span>
    <span class="action-button" style="left:179px;top:276px;width:131px;">Delete</span>
  </section>
</body>
</html>
```